Hartwell Estates Business Cards

I would like a business card that includes myself and my partner.
Includes: Logo, office #, email, website, our names, our numbers and possibly the address. I would also like the logo to be embossed and the card to be horizontal.
There is a photo of our yard signs to give you an idea of the colors of our business.

Target Market(s)

Everyone in real estate market.
We are in a rural area. Our clientele are from all socioeconomic backgrounds.

Industry/Entity Type

Real Estate Agent

Contact Information for Business Card

Company Name: Hartwell Estates
Our Names, Titles & Cell #'s : Dana Pembrook-Broker (555).317.6624, Marla Pembrook-Realtor (555).609.1385
Office #: (555).240.3918
Website: hartwellestates-demo.com
Joint Email: pembrook@hartwellestates-demo.com
Office Address: 418B W. Calloway Ave.
Ashcombe, TN. 70913

Font styles to use
Serif

Requirements
Must have
• HORIZONTAL, Logo, Myself and my partners names, Our cell #'s, our office #, our website, our email address
Nice to have
• Embossed logo, office address, our titles.

```html
<!DOCTYPE html>
<html lang="en">
<head>
<meta charset="utf-8">
<title>Hartwell Estates Business Card</title>
<link href="https://fonts.googleapis.com/css2?family=Montserrat:wght@400;600;700&display=swap" rel="stylesheet">
<style>
  :root {
    --bg: #e9e6e1;
    --paper: #f7f7f5;
    --purple: #5a1590;
    --purple-deep: #3f0a6b;
    --purple-light: #7a2cb5;
    --emboss: #d2d2ce;
    --ink-light: #ffffff;
  }
  * { margin: 0; padding: 0; box-sizing: border-box; }
  html, body {
    width: 1200px; height: 1022px; overflow: hidden;
    background: var(--bg);
    font-family: "Montserrat", sans-serif;
  }
  .card {
    position: absolute; left: 150px; top: 254px;
    width: 900px; height: 514px;
    border-radius: 24px; overflow: hidden;
    background: var(--paper);
    box-shadow: 0 12px 30px rgba(0,0,0,0.18);
    display: flex;
  }
  .brand-side {
    width: 392px; height: 100%; flex: none;
    background: var(--paper);
    display: flex; align-items: center; justify-content: center;
    gap: 18px; padding: 0 30px;
  }
  .brand-mark {
    width: 40px; height: 40px; border-radius: 50%; flex: none;
    background: var(--purple);
  }
  .brand-name {
    font-weight: 600; font-size: 34px; letter-spacing: 3px;
    color: var(--emboss); line-height: 1.2;
    text-transform: uppercase;
  }
  .divider { width: 24px; height: 100%; display: flex; flex: none; }
  .divider .rule-purple { width: 8px; background: var(--purple); margin-left: 4px; }
  .divider .rule-gap { width: 8px; background: var(--paper); }
  .contact-side {
    flex: 1; height: 100%; min-width: 0;
    background: linear-gradient(135deg, var(--purple-light) 0%, var(--purple) 45%, var(--purple-deep) 100%);
    color: var(--ink-light);
    padding: 56px 28px 0 40px;
  }
  .person { margin-bottom: 16px; }
  .person-name { font-weight: 600; font-size: 32px; line-height: 1.15; white-space: nowrap; }
  .person-title, .person-phone { font-size: 20px; line-height: 1.3; opacity: 0.92; }
  .address { font-size: 20px; line-height: 1.3; margin-bottom: 16px; opacity: 0.92; }
  .office-line {
    display: flex; align-items: center; gap: 12px;
    font-size: 18px; line-height: 1.6; opacity: 0.95;
    white-space: nowrap;
  }
  .office-line svg { width: 16px; height: 16px; flex: none; }
  .office-line strong { font-weight: 700; }
</style>
</head>
<body>
  <div class="card">
    <div class="brand-side">
      <span class="brand-mark"></span>
      <span class="brand-name">Hartwell<br>Estates</span>
    </div>
    <div class="divider">
      <span class="rule-purple"></span>
      <span class="rule-gap"></span>
    </div>
    <div class="contact-side">
      <div class="person">
        <div class="person-name">Dana Pembrook</div>
        <div class="person-title">Broker</div>
        <div class="person-phone">(555).317.6624</div>
      </div>
      <div class="person">
        <div class="person-name">Marla Pembrook</div>
        <div class="person-title">Realtor</div>
        <div class="person-phone">(555).609.1385</div>
      </div>
      <div class="address">418B W. Calloway Ave.<br>Ashcombe, TN. 70913</div>
      <div class="office-line">
        <svg viewBox="0 0 24 24" fill="#fff"><path d="M6.6 10.8a15 15 0 0 0 6.6 6.6l2.2-2.2a1 1 0 0 1 1-.25 11.4 11.4 0 0 0 3.6.57 1 1 0 0 1 1 1V20a1 1 0 0 1-1 1A17 17 0 0 1 3 4a1 1 0 0 1 1-1h3.5a1 1 0 0 1 1 1c0 1.25.2 2.45.57 3.6a1 1 0 0 1-.25 1z"/></svg>
        <span>(555).240.3918</span>
      </div>
      <div class="office-line">
        <svg viewBox="0 0 24 24" fill="none" stroke="#fff" stroke-width="2"><rect x="3" y="5" width="18" height="14" rx="1"/><path d="M3 6l9 7 9-7"/></svg>
        <span>pembrook@hartwellestates-demo.com</span>
      </div>
      <div class="office-line">
        <svg viewBox="0 0 24 24" fill="none" stroke="#fff" stroke-width="2"><circle cx="12" cy="12" r="9"/><path d="M3 12h18M12 3c3 3 3 15 0 18M12 3c-3 3-3 15 0 18"/></svg>
        <span>www.<strong>hartwellestates-demo</strong>.com</span>
      </div>
    </div>
  </div>
</body>
</html>
```